Software Product Flyer Design

A established czech software company needs a marketing flyer to promote their software product and its modules.
The overall feel of the flyer must to be serious, but also eye-catching, enticing, clever and bold to attract customers.
Unifying graphic element is the new product logo.
The flyer would be A4, colour both sides and folded once (to give 4 pages of A5).
Title page - product logo with module name and module icon, short presentation of the product and list of its key features.
Inside pages - detailed informations with screenshots or graphical schemas.
Back side - informations about technical requirements and user support, contacts (address, phone, fax, e-mail, web pages - no social networks).
Product logo, module icon and some images attached.
Updates
Hello,
Reason: For organizational reasons we extending the deadline by 10 days.
FYI: We have uploaded the new ZIP file with previous version of our flyer.
Attached PDF file with text for inner pages.
Target Market(s)
Existing or new customers like municipalities, public authorities and nonprofit organizations.
Industry/Entity Type
Marketing
Requirements
Must have
- Winning designer must provide a template for Adobe InDesign based on his graphic design.
Avoid to using exotic fonts - in Czech we use Latin Extended characters (like áéěíýůčřžšťďň).
Nice to have
- Using graphic motif from product logo like as attached splash screen.

```html
<!DOCTYPE html>
<html lang="en">
<head>
<meta charset="utf-8">
<title>Nuvaro – Software Flyer</title>
<link rel="stylesheet" href="https://fonts.googleapis.com/css2?family=EB+Garamond:ital,wght@0,400;0,500;1,400&family=Montserrat:wght@400;600&display=swap">
<style>
  :root {
    --backdrop: #e9e6e1;
    --orange: #f05a22;
    --orange-deep: #dc5220;
    --slate: #434a53;
    --slate-map: #4d545d;
    --white: #ffffff;
    --icon-light: #dbe7f5;
    --icon-mid: #b5cbe6;
    --icon-rim: #9aa3ad;
  }
  * { margin: 0; padding: 0; box-sizing: border-box; }
  html, body {
    width: 1200px;
    height: 896px;
    overflow: hidden;
    background: var(--backdrop);
  }
  .flyer {
    position: absolute;
    left: 20px;
    top: 38px;
    width: 1160px;
    height: 820px;
    display: flex;
    box-shadow: 0 4px 14px rgba(0,0,0,0.25);
  }
  .page {
    position: relative;
    width: 580px;
    height: 820px;
  }
  .page--back { background: var(--orange); }
  .page--front { background: var(--slate); }

  .back-motif {
    position: absolute;
    left: 51px;
    top: 123px;
    width: 474px;
    height: 472px;
    border-radius: 60px;
    background: radial-gradient(ellipse at 45% 45%, var(--orange-deep), var(--orange) 72%);
  }

  .wordmark {
    position: absolute;
    display: flex;
    align-items: center;
    gap: 12px;
    font-family: "Montserrat", sans-serif;
    font-weight: 600;
    color: var(--white);
    letter-spacing: -1px;
    line-height: 1;
  }
  .wordmark__square {
    display: block;
    background: var(--white);
    border-radius: 6px;
  }

  .page--back .wordmark {
    left: 35px;
    top: 668px;
    font-size: 52px;
  }
  .page--back .wordmark__square { width: 34px; height: 34px; }

  .contact {
    position: absolute;
    left: 287px;
    top: 672px;
    font-family: "EB Garamond", serif;
    font-style: italic;
    font-size: 14px;
    line-height: 18px;
    color: var(--white);
    list-style: none;
  }
  .contact__address { margin-top: 4px; }
  .contact__web { margin-top: 8px; letter-spacing: 1px; }

  .module-icon {
    position: absolute;
    left: 139px;
    top: 136px;
    width: 301px;
    height: 288px;
    border-radius: 8px;
    background: linear-gradient(160deg, var(--icon-light), var(--icon-mid));
    border: 4px solid var(--icon-rim);
  }
  .module-name {
    position: absolute;
    left: 0;
    right: 0;
    top: 436px;
    text-align: center;
    font-family: "EB Garamond", serif;
    font-weight: 500;
    font-size: 19px;
    letter-spacing: 4px;
    color: var(--white);
  }
  .world-map {
    position: absolute;
    left: 73px;
    top: 502px;
    width: 477px;
    height: 157px;
    border-radius: 40px;
    background: radial-gradient(ellipse at center, var(--slate-map), var(--slate) 75%);
  }
  .page--front .wordmark {
    left: 0;
    right: 0;
    top: 634px;
    justify-content: center;
    font-size: 64px;
  }
  .page--front .wordmark__square {
    width: 38px;
    height: 38px;
    background: var(--orange);
  }
  .tagline {
    position: absolute;
    left: 0;
    right: 0;
    top: 720px;
    text-align: center;
    font-family: "Montserrat", sans-serif;
    font-weight: 400;
    font-size: 15px;
    letter-spacing: 3.5px;
    color: var(--white);
  }
  .website {
    position: absolute;
    left: 0;
    right: 0;
    top: 743px;
    text-align: center;
    font-family: "EB Garamond", serif;
    font-style: italic;
    font-size: 16px;
    letter-spacing: 6px;
    color: var(--orange);
  }
</style>
</head>
<body>
  <main class="flyer">
    <section class="page page--back">
      <div class="back-motif" role="img" aria-label="Large faint decorative motif of overlapping rounded shapes in deeper orange"></div>
      <div class="wordmark"><span class="wordmark__square"></span>nuvaro</div>
      <ul class="contact">
        <li>P : 0123.456.789</li>
        <li>F : 0123.456.789</li>
        <li>E : info@nuvaro.com</li>
        <li class="contact__address">Suite300, Cityname, Countryname 0000.</li>
        <li class="contact__web">www.nuvaro.com</li>
      </ul>
    </section>

    <section class="page page--front">
      <div class="module-icon" role="img" aria-label="Module icon: spiral-bound address book with a large letter A and coloured index tabs"></div>
      <p class="module-name">00000 SOFTWARE</p>
      <div class="world-map" role="img" aria-label="Faint dotted world map"></div>
      <div class="wordmark"><span class="wordmark__square"></span>nuvaro</div>
      <p class="tagline">CZECH SOFTWARE COMPANY</p>
      <p class="website">www.nuvaro.com</p>
    </section>
  </main>
</body>
</html>
```